Agrarhandel benötigt Homepage
Zielgruppe
Wir sind ein Agrarhandel mit einem Warenumschlagslager im Sinne eines klassischen Einzelhandels und vertreiben Produkte an Landwirte.
Wir vertreiben folgende Hauptproduktgruppen:
Einzelfuttermittel
wie z.B. Sojaexktraktionsschrot. Die einzelnen Produkte könnten z.B. wie die Futtermittel auf folgender Seite dargestellt werden (https://www.kornprobe-beispiel.eu/de/produkt/trelomixan)
Mischfuttermittel
Hier bieten wir unseren Kunden an, individuelles Mischfutter auf Basis unserer Einzelfuttermittel herzustellen.
Weitere Details und weitere Produktbereiche habe ich in einer Powerpoint-Übersicht dargestellt.
Neben diesen Produkten wollen wir uns als Familienunternehmen selbst vorstellen. Zudem betreiben wir in unserer Familie zusätzlich einen Milchviehbetrieb den wir ebenfalls hervorheben möchten, da wir unseren Kunden gegenüber einerseits als Zulieferer aber auch als Kollege auftreten wollen.
Einzelfuttermittel: Hier können wir durch unsere Unabhängigkeit punkten, da wir nicht abhängig von bestimmten Lieferanten sind und dementsprechend unabhängig beraten können. Wir untersuchen im Vergleich zu unseren Wettbewerben die Qualität der Futtermittel bis ins Detail und können daher eine Transparenz bieten, die Konkurrenten in der Regel nicht bieten können. Unser Warenumschlagsplatz mit moderner Technik ermöglicht es uns äußerst kosteneffizient die Waren umschlagen und ausliefern zu können.
Mischfuttermittel: Auf Basis der vorhandenen Einzelfuttermittel stellen wir je nach Kundenwunsch individuelle Mischfutter her. Wir arbeiten mit offenen Deklarationen, sodass unsere Kunden jederzeit nachvollziehen können, ob auch die Einzelfuttermittel verwendet wurden, die sie bestellt haben und keine billigen Ersatzprodukte verwendet wurden.
Zudem sind wir BT und HUPA zertifiziert. Die aktuellen für unser Unternehmen ausgestellten Zertifikate müssen für unsere Kunden als Download zur Verfügung stehen. Statt dem HUPA-Logo bitte das ..
Aufgabenstellung
Wir möchten gerne ein zeitgemäße Homepage, jedoch muss auch berücksichtigt werden, dass unsere Kunden eher konservativ denken.

```html
<!DOCTYPE html>
<html lang="de">
<head>
<meta charset="utf-8">
<title>Futterrechner – Weidenkamp Agrar</title>
<link href="https://fonts.googleapis.com/css2?family=DM+Sans:wght@300;400;500&display=swap" rel="stylesheet">
<style>
:root{
  --page:#ffffff;
  --card:#f1f1f1;
  --green:#1d6b50;
  --green-dark:#125a40;
  --orange:#f9a923;
  --track:#cfcfcf;
  --text:#3a3a3a;
  --white:#ffffff;
  --contact:#2a1a12;
}
*{box-sizing:border-box;margin:0;padding:0}
html,body{width:1200px;height:2298px;overflow:hidden;background:var(--page);font-family:"DM Sans",Arial,sans-serif;color:var(--text)}
.screen{position:absolute;left:96px;width:1000px;height:660px;overflow:hidden;box-shadow:0 10px 40px rgba(0,0,0,.35)}
.screen-1{top:70px}.screen-2{top:793px}.screen-3{top:1507px}
.hero-photo{position:absolute;inset:0;background:
  radial-gradient(ellipse 260px 300px at 60px 340px,rgba(150,95,60,.75),transparent 70%),
  radial-gradient(ellipse 380px 120px at 330px 640px,rgba(170,150,130,.55),transparent 70%),
  radial-gradient(ellipse 300px 400px at 900px 500px,rgba(95,85,70,.6),transparent 70%),
  linear-gradient(180deg,#1a0e08 0%,#2b1a10 40%,#3a2a1e 100%)}
.brand{position:absolute;left:66px;top:52px;display:flex;align-items:center;gap:8px;color:var(--white);font-size:15px;font-weight:500;letter-spacing:.5px}
.brand-dot{width:14px;height:14px;border-radius:50%;background:var(--white)}
.main-nav{position:absolute;right:104px;top:55px;display:flex;align-items:center;gap:21px;font-size:10px;color:var(--white);text-transform:uppercase;letter-spacing:.1px}
.nav-shop{background:var(--orange);padding:0 15px;height:22px;line-height:22px;margin-left:1px}
.caret{display:inline-block;width:5px;height:5px;border-right:1px solid #fff;border-bottom:1px solid #fff;transform:rotate(45deg) translate(-1px,-2px);margin-left:4px}
.card{position:absolute;left:103px;top:143px;width:796px;height:446px;background:var(--card)}
.step-title{position:absolute;left:33px;top:32px;font-size:27px;line-height:25px;font-weight:400;color:var(--green)}
.step-title.single{top:57px}
.progress{position:absolute;left:34px;top:90px;width:349px;height:7px;background:var(--track)}
.progress span{display:block;height:100%;background:var(--orange)}
.hint{position:absolute;left:0;right:0;top:154px;text-align:center;font-size:11px;line-height:14px;font-weight:300}
.slider{position:absolute;left:224px;top:211px;width:348px;height:7px;background:var(--track)}
.slider .fill{height:100%;background:var(--green-dark)}
.slider .thumb{position:absolute;top:-6px;width:19px;height:19px;border-radius:50%;background:var(--orange);margin-left:-9px}
.value{position:absolute;left:356px;top:241px;width:85px;height:28px;border:1px solid #9a9a9a;text-align:center;line-height:26px;font-size:11px;font-weight:300}
.btn{position:absolute;height:28px;line-height:28px;text-align:center;font-size:12px;text-transform:uppercase;font-weight:300}
.btn-next{background:var(--orange);color:var(--white);width:80px}
.btn-back{border:1.5px solid #333;color:#333;width:85px;line-height:25px;background:transparent}
.nutrients{position:absolute;left:35px;top:122px;font-size:10.5px;line-height:14px;font-weight:300;list-style:none}
.nutrients .gap{height:12px}
.result-text{position:absolute;left:225px;width:350px;top:158px;text-align:center;font-size:11px;line-height:14px;font-weight:300}
.product-name{position:absolute;left:0;right:0;top:196px;text-align:center;font-size:34px;font-weight:300;color:var(--green);letter-spacing:.5px}
.watchlist{position:absolute;left:346px;top:304px;display:flex;align-items:center;gap:6px;font-size:9px;text-transform:uppercase}
.contact-bar{position:absolute;right:0;top:514px;display:flex;flex-direction:column;gap:6px}
.contact-bar div{width:45px;height:45px;background:var(--contact);display:flex;align-items:center;justify-content:center}
.scroll-hint{position:absolute;left:488px;top:625px}
.nav-dots{position:absolute;left:555px;top:138px;width:16px;height:4px;border-left:2px solid #1d6b50;border-right:2px solid #1d6b50}
</style>
</head>
<body>

<!-- Schritt 1 -->
<section class="screen screen-1">
  <div class="hero-photo" role="img" aria-label="Nahaufnahme einer Kuh auf der Weide, dunkel gehaltenes Hintergrundfoto"></div>
  <div class="brand"><span class="brand-dot"></span>Weidenkamp</div>
  <nav class="main-nav"><span>Über uns</span><span>Produkte<i class="caret"></i></span><span>Partner</span><span>Downloads</span><span>Kontakt</span><span class="nav-shop">Onlineshop</span></nav>
  <div class="nav-dots"></div>
  <div class="card">
    <h2 class="step-title">Schritt 1:<br>Rohprotein</h2>
    <div class="progress"><span style="width:20%"></span></div>
    <p class="hint">Geben Sie die Gehalt an Rohprotein an, um die exakte<br>Zusammensetzung des Futters zu bestimmen.</p>
    <div class="slider"><div class="fill" style="width:27%"></div><span class="thumb" style="left:27%"></span></div>
    <div class="value">27%</div>
    <div class="btn btn-next" style="left:358px;top:387px">Weiter</div>
  </div>
  <div class="contact-bar">
    <div><svg width="22" height="16" viewBox="0 0 22 16" fill="none" stroke="#fff" stroke-width="1.4"><rect x="1" y="1" width="20" height="14"/><path d="M1 1l10 8 10-8M1 15l7-7M21 15l-7-7"/></svg></div>
    <div><svg width="12" height="22" viewBox="0 0 12 22" fill="none" stroke="#fff" stroke-width="1.4"><rect x="1" y="1" width="10" height="20" rx="1.5"/><path d="M4 17h4"/></svg></div>
    <div><svg width="22" height="22" viewBox="0 0 22 22" fill="none" stroke="#fff" stroke-width="1.4"><path d="M3 20l1.3-4.2A9 9 0 1 1 7.6 19z"/><path d="M8 7c0 4 3 7 7 7l1-2-2-1-1 1c-1-.5-2.5-2-3-3l1-1-1-2z"/></svg></div>
  </div>
  <svg class="scroll-hint" width="24" height="34" viewBox="0 0 24 34" fill="none" stroke="#fff" stroke-width="1.5"><rect x="1" y="1" width="22" height="32" rx="11"/><path d="M12 7v12M7 14l5 5 5-5"/></svg>
</section>

<!-- Schritt 2 -->
<section class="screen screen-2">
  <div class="hero-photo" role="img" aria-label="Nahaufnahme einer Kuh auf der Weide, dunkel gehaltenes Hintergrundfoto"></div>
  <div class="brand"><span class="brand-dot"></span>Weidenkamp</div>
  <nav class="main-nav"><span>Über uns</span><span>Produkte<i class="caret"></i></span><span>Partner</span><span>Downloads</span><span>Kontakt</span><span class="nav-shop">Onlineshop</span></nav>
  <div class="nav-dots"></div>
  <div class="card">
    <h2 class="step-title">Schritt 2:<br>Phosphor</h2>
    <div class="progress"><span style="width:40%"></span></div>
    <p class="hint" style="top:157px">Geben Sie den gewünschten Phosphor wert an, um die exakte<br>Zusammensetzung des Futters zu bestimmen.</p>
    <div class="slider" style="top:213px"><div class="fill" style="width:34%"></div><span class="thumb" style="left:34%"></span></div>
    <div class="value" style="top:239px">0,34%</div>
    <div class="btn btn-back" style="left:291px;top:386px">Zurück</div>
    <div class="btn btn-next" style="left:421px;top:386px">Weiter</div>
  </div>
  <div class="contact-bar">
    <div><svg width="22" height="16" viewBox="0 0 22 16" fill="none" stroke="#fff" stroke-width="1.4"><rect x="1" y="1" width="20" height="14"/><path d="M1 1l10 8 10-8M1 15l7-7M21 15l-7-7"/></svg></div>
    <div><svg width="12" height="22" viewBox="0 0 12 22" fill="none" stroke="#fff" stroke-width="1.4"><rect x="1" y="1" width="10" height="20" rx="1.5"/><path d="M4 17h4"/></svg></div>
    <div><svg width="22" height="22" viewBox="0 0 22 22" fill="none" stroke="#fff" stroke-width="1.4"><path d="M3 20l1.3-4.2A9 9 0 1 1 7.6 19z"/><path d="M8 7c0 4 3 7 7 7l1-2-2-1-1 1c-1-.5-2.5-2-3-3l1-1-1-2z"/></svg></div>
  </div>
  <svg class="scroll-hint" width="24" height="34" viewBox="0 0 24 34" fill="none" stroke="#fff" stroke-width="1.5"><rect x="1" y="1" width="22" height="32" rx="11"/><path d="M12 7v12M7 14l5 5 5-5"/></svg>
</section>

<!-- Ergebnis -->
<section class="screen screen-3">
  <div class="hero-photo" role="img" aria-label="Nahaufnahme einer Kuh auf der Weide, dunkel gehaltenes Hintergrundfoto"></div>
  <div class="brand"><span class="brand-dot"></span>Weidenkamp</div>
  <nav class="main-nav"><span>Über uns</span><span>Produkte<i class="caret"></i></span><span>Partner</span><span>Downloads</span><span>Kontakt</span><span class="nav-shop">Onlineshop</span></nav>
  <div class="nav-dots"></div>
  <div class="card">
    <h2 class="step-title single">Ergebniss</h2>
    <div class="progress" style="top:92px"><span style="width:100%"></span></div>
    <ul class="nutrients">
      <li>Rohprotein: 28%</li><li>UDP: 35%</li><li>NXP: 205 g/kg</li><li>RNB: 12 g/kg</li><li>Rohfett: 2,5%</li>
      <li class="gap"></li>
      <li>Rohfaser: 6.5%</li><li>Stärke + Zucker: 27-30%</li><li>Calcium: 0,40%</li><li>Phosphor: 0.50%</li><li>Natrium: 0,10%</li>
    </ul>
    <p class="result-text">Basierend auf den von Ihnen angegebenen Informationen freuen wir uns, Ihnen das ideale Futter für Ihr Tier vorzuschlagen.</p>
    <p class="product-name">WEIDE-MIX 28/4 WK</p>
    <div class="btn btn-next" style="left:346px;top:258px;width:103px">Anfragen</div>
    <div class="watchlist"><svg width="14" height="10" viewBox="0 0 14 10" fill="none" stroke="#333" stroke-width="1.3"><path d="M0 1h9M0 5h9M0 9h6M11 5v5M8.5 7.5h5"/></svg>Auf die Merkliste</div>
    <div class="btn btn-back" style="left:31px;top:385px">Zurück</div>
  </div>
  <div class="contact-bar">
    <div><svg width="22" height="16" viewBox="0 0 22 16" fill="none" stroke="#fff" stroke-width="1.4"><rect x="1" y="1" width="20" height="14"/><path d="M1 1l10 8 10-8M1 15l7-7M21 15l-7-7"/></svg></div>
    <div><svg width="12" height="22" viewBox="0 0 12 22" fill="none" stroke="#fff" stroke-width="1.4"><rect x="1" y="1" width="10" height="20" rx="1.5"/><path d="M4 17h4"/></svg></div>
    <div><svg width="22" height="22" viewBox="0 0 22 22" fill="none" stroke="#fff" stroke-width="1.4"><path d="M3 20l1.3-4.2A9 9 0 1 1 7.6 19z"/><path d="M8 7c0 4 3 7 7 7l1-2-2-1-1 1c-1-.5-2.5-2-3-3l1-1-1-2z"/></svg></div>
  </div>
  <svg class="scroll-hint" width="24" height="34" viewBox="0 0 24 34" fill="none" stroke="#fff" stroke-width="1.5"><rect x="1" y="1" width="22" height="32" rx="11"/><path d="M12 7v12M7 14l5 5 5-5"/></svg>
</section>

</body>
</html>
```